Tidal Forge - Crypto Currency Miner Powered by Renewable Energy Website

We Need Web Pages Design for Website for Crypto Currency Miner

Serivices include:
Mining Rig Sales
Housing for Rigs turnkey on renewable energy grid
Cloud Mining term packages
Updates

http://www.vaultrigsurvey.example (Competitors sites)

Target Market(s)

Investers for Mining Rigs and terms for 1,2 or 3 years of Hash rate

Industry/Entity Type

Mining

Number of Pages Required

5+ page

Font styles to use
Sans Serif

Colors
add136
9bcb3c
606060
474747
ffc214
cadf82
fbee3e
876aae
6b449b

Requirements
Must have
• Pictures of Solar, Wind and power Factor Correction units
Nice to have
• e-commerce platform so contract terms can be purchased through website
Should not have
• Heavy construction equipment

```html
<!DOCTYPE html>
<html lang="en">
<head>
<meta charset="utf-8">
<title>Tidal Forge – Renewable Crypto Mining</title>
<link href="https://fonts.googleapis.com/css2?family=Oswald:wght@300;400;500&family=Roboto+Condensed:wght@300;400;700&family=Roboto:wght@400;500&display=swap" rel="stylesheet">
<style>
:root{
  --green:#8dc63f;
  --green-dark:#7ab52e;
  --yellow:#ffc214;
  --lemon:#fbee3e;
  --grey:#606060;
  --charcoal:#474747;
  --ink:#333333;
  --backdrop:#ececec;
  --logo-box:#e9e9e9;
  --white:#ffffff;
}
*{margin:0;padding:0;box-sizing:border-box}
html,body{width:1200px;height:1200px;overflow:hidden;background:var(--backdrop)}
body{position:relative;font-family:"Roboto Condensed",sans-serif}
.page{position:absolute;left:322px;top:36px;width:555px;height:1164px;overflow:hidden;background:var(--white);box-shadow:10px 10px 22px rgba(0,0,0,.18)}
.abs{position:absolute}
.bg{position:absolute;left:0;top:0}
.logo-box{left:91px;top:6px;width:93px;height:92px;background:var(--logo-box);display:flex;flex-direction:column;align-items:center;justify-content:center;gap:8px}
.logo-dot{width:28px;height:28px;border-radius:50%;background:var(--green)}
.logo-name{font-family:"Roboto Condensed",sans-serif;font-weight:700;font-size:15px;color:var(--green)}
.nav{top:30px;left:220px;display:flex;gap:0;font-family:"Roboto",sans-serif;font-size:6px;letter-spacing:.4px;color:var(--white)}
.nav span{position:absolute;white-space:nowrap}
.hero-kicker{left:96px;top:122px;font-size:8.5px;line-height:10.5px;color:var(--white)}
.hero-title{left:94px;top:148px;font-family:"Oswald",sans-serif;font-weight:400;font-size:37px;line-height:38px;color:var(--white);letter-spacing:-.5px}
.hero-copy{left:96px;top:270px;width:180px;font-size:4.6px;line-height:6.5px;color:var(--white)}
.btn-dark{left:96px;top:304px;width:96px;height:21px;border-radius:3px;background:var(--ink);color:var(--white);font-size:10px;display:flex;align-items:center;justify-content:center}
.login{left:366px;top:222px;width:89px;height:142px;border-radius:9px;background:linear-gradient(var(--lemon) 0 22%,var(--yellow) 22% 100%);box-shadow:0 2px 5px rgba(0,0,0,.2)}
.login-badge{left:15px;top:-21px;width:58px;height:58px;border-radius:50%;background:var(--green);border:5px solid var(--white);box-shadow:0 2px 4px rgba(0,0,0,.25)}
.field{left:10px;width:67px;height:13px;border-radius:7px;background:var(--white);font-size:4.5px;color:#aaa;display:flex;align-items:center;padding-left:16px;letter-spacing:.3px}
.field svg{position:absolute;left:5px;top:3px}
.remember{left:21px;top:100px;font-size:3.6px;color:var(--white);display:flex;align-items:center;gap:3px}
.remember i{display:block;width:5px;height:5px;border-radius:50%;background:var(--white);border:1.5px solid var(--ink)}
.login-btn{left:25px;top:112px;width:40px;height:14px;border-radius:7px;background:var(--lemon);border:1px solid var(--white);color:#e0a900;font-size:5px;display:flex;align-items:center;justify-content:center}
.register{left:14px;top:133px;font-size:3.2px;color:var(--white);white-space:nowrap}
.register b{color:var(--ink)}
.feature{top:388px;width:130px;text-align:center;color:var(--charcoal)}
.feature svg{display:block;margin:0 auto}
.feature h3{margin-top:12px;font-family:"Oswald",sans-serif;font-weight:300;font-size:12.5px;line-height:14.5px;color:var(--charcoal)}
.feature p{margin:14px auto 0;width:92px;font-size:5.4px;line-height:7.3px;color:var(--ink)}
.btn-line{display:inline-flex;align-items:center;justify-content:center;width:58px;height:13px;border:1px solid #555;border-radius:2px;font-size:6px;color:var(--ink);margin-top:10px}
.feature .btn-line.yellow{border-color:var(--yellow)}
.feature .btn-line.green{border-color:var(--green)}
.divider{top:386px;width:1px;height:174px;background:#9a9a9a}
.buy-title{left:84px;top:666px;font-family:"Oswald",sans-serif;font-weight:400;font-size:20px;line-height:24px;color:var(--white)}
.bar{height:3px}
.lead{font-size:8.4px;line-height:10.5px;color:var(--white);text-align:justify}
.small{font-size:4.6px;line-height:7.4px;color:var(--white);text-align:justify}
.btn-ghost{display:flex;align-items:center;justify-content:center;height:13px;border:1px solid var(--white);border-radius:2px;font-size:6px;color:var(--white)}
.tablet{left:290px;top:605px;width:236px;height:290px;border-radius:16px;background:#1c1c1c;transform:rotate(9deg);box-shadow:-4px 6px 12px rgba(0,0,0,.35);padding:12px 12px 22px}
.tablet-screen{width:100%;height:100%;border-radius:3px;background:radial-gradient(circle at 55% 60%,#2d78c8 0 30%,#7fb4e6 31%,#b9d8f4 100%)}
.why-title{left:305px;top:932px;font-family:"Oswald",sans-serif;font-weight:400;font-size:17px;color:var(--white);white-space:nowrap;letter-spacing:-.3px}
.why-title em{font-style:normal;color:var(--green)}
.tile{width:76px;height:76px;border-radius:3px;display:flex;flex-direction:column;align-items:center;justify-content:flex-end;padding-bottom:7px;gap:6px;font-family:"Oswald",sans-serif;font-size:10px;line-height:11px;text-align:center;color:var(--white)}
.tile.green{background:var(--green)}
.tile.orange{background:var(--yellow)}
.tile.lemon{background:var(--lemon);color:var(--ink)}
.tile.plain{background:var(--white);color:var(--ink)}
</style>
</head>
<body>
<main class="page">
  <svg class="bg" width="555" height="1164" viewBox="0 0 555 1164">
    <defs>
      <linearGradient id="heroShade" x1="0" y1="0" x2="1" y2="1">
        <stop offset="0" stop-color="#6a6a6a"/>
        <stop offset=".55" stop-color="#4a4a4a"/>
        <stop offset="1" stop-color="#2e2e2e"/>
      </linearGradient>
    </defs>
    <polygon points="0,0 555,0 555,292 0,384" fill="url(#heroShade)" role="img" aria-label="Greyscale photo of a wind turbine rising over farmland under a cloudy sky"/>
    <polygon points="170,0 555,0 555,32" fill="var(--yellow)"/>
    <polygon points="0,664 555,574 555,856 0,944" fill="var(--green)"/>
    <polygon points="0,944 555,856 555,1164 0,1164" fill="var(--charcoal)"/>
  </svg>

  <!-- Header -->
  <div class="abs logo-box"><span class="logo-dot"></span><span class="logo-name">Tidal Forge</span></div>
  <nav class="abs nav">
    <span style="left:0">HOME</span>
    <span style="left:38px">PRICING</span>
    <span style="left:87px">OUR OFFER</span>
    <span style="left:137px">ABOUT US</span>
    <span style="left:188px">CUSTOMER SERVICE</span>
  </nav>

  <!-- Hero -->
  <p class="abs hero-kicker">Join over 1.000.000 people with the<br>world's leading hashpower provider</p>
  <h1 class="abs hero-title">START<br>TIDAL FORGE<br>TODAY!</h1>
  <p class="abs hero-copy">It's super simple - Your mining rigs are already set up and running. As soon as you've set-up your account you can start to earn your first coins from our bitcoin cloud mining service!</p>
  <a class="abs btn-dark">Learn More</a>

  <form class="abs login">
    <span class="abs login-badge"></span>
    <div class="abs field" style="top:56px"><svg width="7" height="7" viewBox="0 0 7 7"><circle cx="3.5" cy="2" r="1.7" fill="#333"/><path d="M0.5 7a3 3 0 0 1 6 0z" fill="#333"/></svg>USERNAME</div>
    <div class="abs field" style="top:77px"><svg width="7" height="7" viewBox="0 0 7 7"><path d="M2 3V2a1.5 1.5 0 0 1 3 0v1" stroke="#333" fill="none"/><rect x="1" y="3" width="5" height="4" fill="#333"/></svg>PASSWORD</div>
    <div class="abs remember"><i></i>Remember Me !</div>
    <div class="abs login-btn">LOG IN</div>
    <div class="abs register">Don't have a account ? <b>REGISTER HERE</b></div>
  </form>

  <!-- Features -->
  <section class="abs feature" style="left:79px">
    <svg width="72" height="78" viewBox="0 0 72 78"><polygon points="36,2 70,21 70,57 36,76 2,57 2,21" fill="var(--yellow)"/><polygon points="36,8 64,24 64,54 36,70 8,54 8,24" fill="none" stroke="#fff" stroke-width="1.5"/><g stroke="#fff" stroke-width="1.3" fill="none"><circle cx="36" cy="39" r="3"/><path d="M36 36l-2-14 4 0z M38.5 40.5l12 7-2 3z M33.5 40.5l-12 7 2 3z"/><circle cx="36" cy="39" r="17" stroke-dasharray="3 4"/></g></svg>
    <h3>WIND POWER<br>INVESTMENT</h3>
    <p>Don't wrestle with rig assembly and hot, noisy miners at home. We have the fastest bitcoin mining hardware running for you already!</p>
    <a class="btn-line yellow">Learn More</a>
  </section>
  <div class="abs divider" style="left:207px"></div>
  <section class="abs feature" style="left:213px">
    <svg width="72" height="78" viewBox="0 0 72 78"><polygon points="36,2 70,21 70,57 36,76 2,57 2,21" fill="var(--green)"/><polygon points="36,8 64,24 64,54 36,70 8,54 8,24" fill="none" stroke="#fff" stroke-width="1.5"/><g stroke="#fff" stroke-width="1.3" fill="none"><circle cx="36" cy="27" r="2.5"/><rect x="22" y="33" width="28" height="14"/><path d="M29 33v14M36 33v14M43 33v14M22 40h28M36 47v6M28 53h16"/></g></svg>
    <h3>SOLAR POWER<br>INVESTMENT</h3>
    <p>Don't wrestle with rig assembly and hot, noisy miners at home. We have the fastest bitcoin mining hardware running for you already!</p>
    <a class="btn-line green">Learn More</a>
  </section>
  <div class="abs divider" style="left:344px"></div>
  <section class="abs feature" style="left:349px">
    <svg width="72" height="78" viewBox="0 0 72 78"><polygon points="36,2 70,21 70,57 36,76 2,57 2,21" fill="var(--charcoal)"/><polygon points="36,8 64,24 64,54 36,70 8,54 8,24" fill="none" stroke="#fff" stroke-width="1.5"/><g stroke="#fff" stroke-width="1.4" fill="none"><rect x="21" y="32" width="30" height="20" rx="2"/><path d="M25 32l14-8 6 8M43 38h8v8h-8z"/><circle cx="46" cy="42" r="1"/></g></svg>
    <h3>GET YOUR FIRST<br>PAYOUT TODAY</h3>
    <p>Don't wrestle with rig assembly and hot, noisy miners at home. We have the fastest bitcoin mining hardware running for you already!</p>
    <a class="btn-line">Learn More</a>
  </section>

  <!-- Buy and sell -->
  <h2 class="abs buy-title">Buy And Sell<br>Crypto Currency Miner</h2>
  <div class="abs bar" style="left:84px;top:718px;width:122px;background:var(--charcoal)"></div>
  <div class="abs bar" style="left:206px;top:718px;width:44px;background:#bfe08a"></div>
  <p class="abs lead" style="left:90px;top:730px;width:160px">Lorem ipsum dolor sit amet, consectetur adipisicing elit. Aliquam praesentium, distinctio dicta molestias dignissimos.</p>
  <p class="abs small" style="left:90px;top:772px;width:160px">Lorem ipsum dolor sit amet, consectetur adipisicing elit. Quam earum, provident ad, porro aperiam dolore, blanditiis, nihil pariatur eius adipisci consequuntur officiis. Excepturi, nostrum? Id incidunt nesciunt officia hic distinctio nihil pariatur.</p>
  <p class="abs small" style="left:90px;top:810px;width:160px">Lorem ipsum dolor sit amet, consectetur adipisicing elit. Quam earum, provident ad, porro aperiam dolore, blanditiis, nihil pariatur eius adipisci consequuntur officiis. Excepturi, nostrum? Id incidunt nesciunt officia hic distinctio nihil pariatur. Lorem ipsum dolor sit amet, consectetur adipisicing elit. Quam earum, provident ad, porro aperiam dolore, blanditiis, nihil pariatur eius adipisci consequuntur officiis. Excepturi, nostrum? Id incidunt nesciunt officia hic distinctio nihil pariatur.</p>
  <a class="abs btn-ghost" style="left:191px;top:872px;width:57px">Learn More</a>

  <div class="abs tablet"><div class="tablet-screen" role="img" aria-label="Tablet screen showing the earth among clouds with solar panels and wind turbines"></div></div>

  <!-- Why choose -->
  <h2 class="abs why-title">Why Choose <em>Tidal Forge</em>?</h2>
  <div class="abs bar" style="left:305px;top:957px;width:45px;height:2px;background:#9a9a9a"></div>
  <div class="abs bar" style="left:350px;top:957px;width:121px;height:2px;background:var(--green)"></div>
  <p class="abs lead" style="left:310px;top:968px;width:161px">Lorem ipsum dolor sit amet, consectetur adipisicing elit. Aliquam praesentium, distinctio dicta molestias dignissimos.</p>
  <p class="abs small" style="left:310px;top:1009px;width:161px">Lorem ipsum dolor sit amet, consectetur adipisicing elit. Quam earum, provident ad, porro aperiam dolore, blanditiis, nihil pariatur eius adipisci consequuntur officiis. Excepturi, nostrum? Id incidunt nesciunt officia hic distinctio nihil pariatur.</p>
  <p class="abs small" style="left:310px;top:1047px;width:161px">Lorem ipsum dolor sit amet, consectetur adipisicing elit. Quam earum, provident ad, porro aperiam dolore, blanditiis, nihil pariatur eius adipisci consequuntur officiis. Excepturi, nostrum? Id incidunt nesciunt officia hic distinctio nihil pariatur. Lorem ipsum dolor sit amet, consectetur adipisicing elit. Quam earum, provident ad, porro aperiam dolore, blanditiis, nihil pariatur eius adipisci consequuntur officiis. Excepturi, nostrum? Id incidunt nesciunt officia hic distinctio nihil pariatur.</p>
  <a class="abs btn-ghost" style="left:412px;top:1110px;width:57px">Learn More</a>

  <div class="abs tile green" style="left:96px;top:966px">
    <svg width="32" height="36" viewBox="0 0 32 36" fill="none" stroke="#fff" stroke-width="1.6"><path d="M16 2l13 5v10c0 9-6 15-13 17C9 32 3 26 3 17V7z"/><path d="M16 7l8 3v7c0 6-4 10-8 12-4-2-8-6-8-12v-7z"/><circle cx="16" cy="16" r="3"/><path d="M16 19v5"/></svg>
    <span>Safe And Secure</span>
  </div>
  <div class="abs tile orange" style="left:191px;top:966px">
    <svg width="36" height="36" viewBox="0 0 36 36" fill="none" stroke="#fff" stroke-width="1.6"><rect x="6" y="2" width="18" height="32" rx="3"/><path d="M13 30h4"/><circle cx="14" cy="13" r="4"/><circle cx="28" cy="22" r="4"/><path d="M28 15v3M28 26v3M21 22h3M32 22h3"/></svg>
    <span>Mobile App</span>
  </div>
  <div class="abs tile lemon" style="left:96px;top:1057px">
    <svg width="36" height="34" viewBox="0 0 36 34" fill="none" stroke="#333" stroke-width="1.6"><rect x="4" y="8" width="28" height="22" rx="2"/><path d="M8 8l12-6 6 6M24 15h8v8h-8z"/><path d="M8 18l6 3v5c0 3-3 5-6 6-3-1-6-3-6-6v-5z" fill="var(--lemon)"/></svg>
    <span>Secure Wallet</span>
  </div>
  <div class="abs tile plain" style="left:191px;top:1057px">
    <svg width="34" height="36" viewBox="0 0 34 36" fill="none" stroke="#333" stroke-width="1.6"><rect x="4" y="5" width="20" height="28" rx="2"/><rect x="10" y="2" width="8" height="5" rx="1"/><path d="M14 11l6 2v5c0 4-3 6-6 7-3-1-6-3-6-7v-5z"/><circle cx="26" cy="27" r="6" fill="#fff"/><path d="M26 24v6M23 27h6"/></svg>
    <span>Covered By<br>Insurance</span>
  </div>
</main>
</body>
</html>
```